business card design for a plumbing contractor

i need a double business card for a plumbing business, our initial service is residential Sewer Drain Cleaning.

Target Market(s)

other plumbing Business

Industry/Entity Type

Plumbing

Contact Information for Business Card

www.PipeworksTopMark.example- 5307218394-

Font styles to use
Serif

Colors
ec1f27
0455a3

```html
<!DOCTYPE html>
<html lang="en">
<head>
<meta charset="utf-8">
<title>Pipeworks Top Mark – Business Card</title>
<link rel="stylesheet" href="https://fonts.googleapis.com/css2?family=Open+Sans:wght@400;600;700&display=swap">
<style>
  :root {
    --stage: #2b2b2b;
    --card-dark: #181818;
    --card-mid: #262626;
    --accent-red: #e8242b;
    --text-white: #ffffff;
    --text-soft: #e6e6e6;
    --text-muted: #cfcfcf;
  }
  * { margin: 0; padding: 0; box-sizing: border-box; }
  html, body {
    width: 1200px; height: 900px; overflow: hidden;
    background: var(--stage);
    font-family: "Open Sans", Arial, sans-serif;
  }
  .stage {
    position: relative; width: 1200px; height: 900px;
    display: flex; flex-direction: column; align-items: center; justify-content: center; gap: 40px;
  }
  .card {
    position: relative; width: 640px; height: 366px;
    background: radial-gradient(ellipse at 70% 40%, var(--card-mid), var(--card-dark) 75%);
    border-bottom: 8px solid var(--accent-red);
    box-shadow: 0 10px 24px rgba(0,0,0,.45);
    overflow: hidden;
  }
  .brand-name {
    font-family: "Open Sans", Arial, sans-serif;
    font-weight: 700; color: var(--text-white);
    line-height: 1.05; letter-spacing: .5px;
    display: flex; align-items: center; gap: 14px;
  }
  .brand-square { width: 22px; height: 22px; background: var(--accent-red); flex: none; }
  .card-front { display: flex; align-items: center; justify-content: center; }
  .card-front .brand-name { font-size: 46px; }
  .card-back .brand-name {
    position: absolute; left: 56px; top: 130px; font-size: 30px;
  }
  .card-back .brand-name .brand-square { width: 16px; height: 16px; }
  .divider {
    position: absolute; left: 290px; top: 72px; width: 2px; height: 190px;
    background: var(--text-white);
  }
  .details { position: absolute; left: 316px; top: 74px; color: var(--text-soft); }
  .person-name {
    font-size: 26px; font-weight: 400; color: var(--accent-red);
    text-transform: uppercase; letter-spacing: .5px; line-height: 1.1;
  }
  .person-role { font-size: 15px; margin-bottom: 12px; }
  .contact-list, .service-list { list-style: none; font-size: 16px; line-height: 1.35; }
  .contact-list li { display: flex; align-items: center; gap: 8px; }
  .contact-list svg { width: 11px; height: 11px; flex: none; }
  .service-list { margin-top: 10px; }
  .service-list li { display: flex; align-items: center; gap: 12px; }
  .service-list li::before {
    content: ""; width: 7px; height: 7px; border-radius: 50%; background: var(--accent-red); flex: none;
  }
</style>
</head>
<body>
<main class="stage">
  <section class="card card-front">
    <div class="brand-name"><span>Pipeworks<br>Top Mark</span><span class="brand-square"></span></div>
  </section>

  <section class="card card-back">
    <div class="brand-name"><span>Pipeworks<br>Top Mark</span><span class="brand-square"></span></div>
    <div class="divider"></div>
    <div class="details">
      <h1 class="person-name">Daniel Harper</h1>
      <p class="person-role">Director</p>
      <ul class="contact-list">
        <li>
          <svg viewBox="0 0 12 12" aria-hidden="true"><path d="M2.5 1 L4.5 1 L5 3.5 L3.8 4.3 Q5 6.8 7.7 8.2 L8.5 7 L11 7.5 L11 9.5 Q10.5 11 9 11 Q1 10 1 3 Q1 1.5 2.5 1 Z" fill="none" stroke="var(--accent-red)" stroke-width="1.1"/></svg>
          5307218394
        </li>
        <li>
          <svg viewBox="0 0 12 12" aria-hidden="true"><rect x="1" y="2.5" width="10" height="7" fill="none" stroke="var(--accent-red)" stroke-width="1.1"/><path d="M1 2.5 L6 6.5 L11 2.5" fill="none" stroke="var(--accent-red)" stroke-width="1.1"/></svg>
          dispatch@PipeworksTopMark.example
        </li>
        <li>
          <svg viewBox="0 0 12 12" aria-hidden="true"><circle cx="6" cy="6" r="5" fill="none" stroke="var(--accent-red)" stroke-width="1.1"/><ellipse cx="6" cy="6" rx="2.2" ry="5" fill="none" stroke="var(--accent-red)" stroke-width="1"/><path d="M1 6 H11" stroke="var(--accent-red)" stroke-width="1"/></svg>
          www.PipeworksTopMark.example
        </li>
      </ul>
      <ul class="service-list">
        <li>Sewer Drain Cleaning</li>
        <li>Maintenance</li>
        <li>Trenchless Pipe Installs.</li>
      </ul>
    </div>
  </section>
</main>
</body>
</html>
```